​Silver Harbor Rhythm provides personal, friendly service in a fun and high energy environment. We are based in Vermont.

We would like a card that appeals to a wide range of audiences as we do a wide range of events. Please feel free to check out our website silverharborrhythm.net for inspiration.

Target Market(s)

weddings, corporate, birthday parties, colleges

Industry/Entity Type

Business

Contact Information for Business Card

Silver Harbor Rhythm
Providing Entertainment For All Occasions
555 274 9160
silverharborrhythm@mailnest.net
silverharborrhythm.net

```html
<!DOCTYPE html>
<html lang="en">
<head>
<meta charset="utf-8">
<title>Silver Harbor Rhythm – Business Card</title>
<link rel="stylesheet" href="https://fonts.googleapis.com/css2?family=Open+Sans:wght@400;600;700&display=swap">
<style>
  :root {
    --page-bg: #ece9e3;
    --card-bg: #ffffff;
    --card-edge: #2a2a2a;
    --brand-green: #2f5410;
    --text-dark: #2b2b2b;
    --mark-tint-top: #f1dede;
    --mark-tint-bottom: #dfe5d8;
  }
  * { box-sizing: border-box; margin: 0; padding: 0; }
  html, body {
    width: 1200px;
    height: 390px;
    overflow: hidden;
    background: var(--page-bg);
    font-family: "Open Sans", Arial, sans-serif;
    color: var(--text-dark);
  }
  .canvas { position: relative; width: 1200px; height: 390px; }
  .card {
    position: absolute;
    top: 32px;
    width: 567px;
    height: 324px;
    background: var(--card-bg);
    border: 1px solid var(--card-edge);
    overflow: hidden;
  }
  .card--front { left: 31px; }
  .card--back { left: 615px; }

  .brand-decoration {
    position: absolute;
    background: linear-gradient(180deg, var(--mark-tint-top) 0%, var(--mark-tint-bottom) 100%);
    opacity: 0.7;
  }
  .card--front .brand-decoration {
    left: 345px; top: 30px; width: 222px; height: 294px;
    border-radius: 120px 0 0 0;
  }
  .card--back .brand-decoration {
    left: 0; top: 30px; width: 190px; height: 294px;
    border-radius: 0 90px 0 0;
  }

  .brand-name {
    position: absolute;
    color: var(--brand-green);
    font-weight: 600;
    text-transform: uppercase;
    letter-spacing: 1px;
    line-height: 1.1;
  }
  .card--front .brand-name {
    left: 26px; top: 78px;
    font-size: 24px;
  }
  .brand-square {
    position: absolute;
    left: 26px; top: 40px;
    width: 26px; height: 26px;
    background: var(--brand-green);
  }

  .person {
    position: absolute;
    left: 26px; top: 174px;
    font-size: 16px;
    color: var(--text-dark);
  }
  .person__name { color: var(--brand-green); font-weight: 700; font-size: 17px; }

  .contact-list {
    position: absolute;
    left: 26px; top: 212px;
    list-style: none;
    font-size: 13px;
  }
  .contact-list li {
    display: flex;
    align-items: center;
    height: 23px;
  }
  .contact-icon { width: 13px; height: 13px; margin-right: 6px; flex: none; }

  .address {
    position: absolute;
    left: 26px; top: 300px;
    font-size: 13px;
  }

  .card--back .brand-name {
    right: 22px; top: 218px;
    font-size: 24px;
    text-align: right;
  }
  .web-address {
    position: absolute;
    right: 22px; top: 286px;
    font-size: 18px;
    letter-spacing: 1.2px;
    color: var(--text-dark);
  }
</style>
</head>
<body>
<main class="canvas">
  <section class="card card--front">
    <div class="brand-decoration" role="img" aria-label="Faint brand decoration area"></div>
    <span class="brand-square" aria-hidden="true"></span>
    <div class="brand-name">Silver Harbor<br>Rhythm</div>

    <p class="person"><span class="person__name">Your Name,</span> Title</p>

    <ul class="contact-list">
      <li>
        <svg class="contact-icon" viewBox="0 0 14 14" aria-hidden="true">
          <circle cx="7" cy="7" r="7" fill="var(--brand-green)"/>
          <path d="M4.6 3.6l1.3 1.6-.7.9c.5 1 1.2 1.7 2.2 2.2l.9-.7 1.6 1.3-.8 1.2C6.4 10 4 7.6 3.8 4.4z" fill="#fff"/>
        </svg>
        555 274 9160
      </li>
      <li>
        <svg class="contact-icon" viewBox="0 0 14 14" aria-hidden="true">
          <circle cx="7" cy="7" r="7" fill="var(--brand-green)"/>
          <rect x="3.5" y="4.5" width="7" height="5" fill="#fff"/>
          <path d="M3.5 4.5L7 7.3l3.5-2.8" fill="none" stroke="var(--brand-green)" stroke-width="0.8"/>
        </svg>
        silverharborrhythm@mailnest.net
      </li>
      <li>
        <svg class="contact-icon" viewBox="0 0 14 14" aria-hidden="true">
          <circle cx="7" cy="7" r="7" fill="var(--brand-green)"/>
          <circle cx="7" cy="7" r="3.6" fill="none" stroke="#fff" stroke-width="0.9"/>
          <path d="M3.4 7h7.2M7 3.4v7.2" stroke="#fff" stroke-width="0.9"/>
        </svg>
        www.silverharborrhythm.net
      </li>
    </ul>

    <p class="address">Sreet Name, City Name, Zip Code-00000</p>
  </section>

  <section class="card card--back">
    <div class="brand-decoration" role="img" aria-label="Faint brand decoration area"></div>
    <div class="brand-name">Silver Harbor<br>Rhythm</div>
    <p class="web-address">www.silverharborrhythm.net</p>
  </section>
</main>
</body>
</html>
```